Alterations to existing business card

Here is my current logo and I want the "cafe and bar" taken off with just the words Lumo and our slogan "Savour the moment" on the card, Plus the logo.
Our Current Business Card is currently 5.5cm by 5.5cm and would like it to remain like this thanks.
The loyalty card can be 10 squares with the logo specifying the 10th coffee free. I would like the cheapest option please.
Also on our business card would like the Facebook logo and instagram Logo with TAZALUMO27 as link to our photos on instagram.

Keep Colour schemes the same please.

On the business cards

Dale Brinton Director
0427916038
dale27lumo@mailvista.test

Paula Ferrisi Principal
0428571963
paulumo@mailvista.test

Thanks Dale

Industry/Entity Type

Business

```html
<!DOCTYPE html>
<html lang="en">
<head>
<meta charset="utf-8">
<title>Lumo – Business Card</title>
<link rel="stylesheet" href="https://fonts.googleapis.com/css2?family=Carlito:wght@400;700&display=swap">
<style>
  :root {
    --backdrop: #2e2622;
    --card: #141414;
    --card-edge: #1c1c1c;
    --gold: #e0a62b;
    --gold-deep: #b9821a;
    --white: #f4f4f4;
    --text-soft: #e6e6e6;
  }
  * { box-sizing: border-box; margin: 0; padding: 0; }
  html, body {
    width: 1200px; height: 716px; overflow: hidden;
    background: var(--backdrop);
    font-family: "Carlito", "Calibri", sans-serif;
  }
  .stage {
    position: relative; width: 1200px; height: 716px;
    display: flex; align-items: center; justify-content: center; gap: 50px;
  }
  .card {
    position: relative; width: 520px; height: 300px;
    background: var(--card);
    border: 1px solid var(--card-edge);
    box-shadow: 0 10px 30px rgba(0,0,0,.45);
  }

  /* brand lockup */
  .brand { position: absolute; display: flex; align-items: center; }
  .brand-ring {
    border: 4px solid var(--gold); border-radius: 50%;
    flex: none;
  }
  .brand-text { display: flex; flex-direction: column; }
  .brand-name {
    color: var(--white); font-weight: 400; letter-spacing: 3px; line-height: 1;
  }
  .brand-slogan {
    color: var(--gold-deep); font-weight: 400; letter-spacing: 1.5px; text-transform: uppercase;
    white-space: nowrap;
  }

  /* contact side */
  .card-contact .brand { left: 150px; top: 26px; gap: 12px; }
  .card-contact .brand-ring { width: 66px; height: 66px; }
  .card-contact .brand-name { font-size: 38px; }
  .card-contact .brand-slogan { font-size: 11px; margin-top: 3px; }

  .person { position: absolute; left: 34px; top: 104px; }
  .person-name { color: var(--gold); font-weight: 700; font-size: 22px; }
  .person-role { color: var(--text-soft); font-size: 15px; margin-top: 2px; }

  .divider {
    position: absolute; left: 26px; right: 26px; top: 156px;
    height: 1px; background: var(--gold-deep);
  }

  .contact-list { position: absolute; left: 34px; top: 174px; list-style: none; }
  .contact-list li {
    display: flex; align-items: center; gap: 10px;
    color: var(--white); font-size: 15px; line-height: 24px;
  }
  .contact-icon { width: 13px; height: 13px; flex: none; }

  .social { position: absolute; right: 32px; bottom: 30px; display: flex; align-items: center; gap: 10px; }
  .social-handle { color: var(--gold); font-size: 16px; letter-spacing: .5px; }
  .social-marks { display: flex; flex-direction: column; gap: 5px; }
  .social-mark { width: 20px; height: 20px; border-radius: 3px; }
  .social-mark.photo { background: #8a6a4a; }
  .social-mark.network { background: #3b5a9a; }

  /* logo side */
  .card-logo .brand { left: 50%; top: 50%; transform: translate(-50%, -50%); gap: 16px; }
  .card-logo .brand-ring { width: 96px; height: 96px; border-width: 5px; }
  .card-logo .brand-name { font-size: 58px; }
  .card-logo .brand-slogan { font-size: 15px; margin-top: 4px; }
</style>
</head>
<body>
<main class="stage">

  <section class="card card-contact" aria-label="Business card, contact side">
    <div class="brand">
      <span class="brand-ring"></span>
      <div class="brand-text">
        <span class="brand-name">LUMO</span>
        <span class="brand-slogan">Savour the moment</span>
      </div>
    </div>

    <div class="person">
      <p class="person-name">Paula Ferrisi</p>
      <p class="person-role">Principal</p>
    </div>

    <div class="divider"></div>

    <ul class="contact-list">
      <li>
        <svg class="contact-icon" viewBox="0 0 13 13" aria-hidden="true">
          <rect width="13" height="13" rx="2" fill="var(--gold)"/>
          <path d="M4 3 l1.5 0 l.6 2 l-1 .8 a5 5 0 0 0 2.2 2.2 l.8-1 l2 .6 l0 1.5 a1 1 0 0 1-1 1 a6.5 6.5 0 0 1-6-6 a1 1 0 0 1 .9-1.1z" fill="var(--card)"/>
        </svg>
        0428571963
      </li>
      <li>
        <svg class="contact-icon" viewBox="0 0 13 13" aria-hidden="true">
          <rect width="13" height="13" rx="2" fill="var(--gold)"/>
          <rect x="2.5" y="3.5" width="8" height="6" fill="var(--card)"/>
          <path d="M2.5 3.5 L6.5 7 L10.5 3.5" stroke="var(--gold)" stroke-width="1" fill="none"/>
        </svg>
        paulumo@mailvista.test
      </li>
      <li>
        <svg class="contact-icon" viewBox="0 0 13 13" aria-hidden="true">
          <rect width="13" height="13" rx="2" fill="var(--gold)"/>
          <path d="M6.5 2.2 a3 3 0 0 1 3 3 c0 2.2-3 5.6-3 5.6 s-3-3.4-3-5.6 a3 3 0 0 1 3-3z" fill="var(--card)"/>
          <circle cx="6.5" cy="5.2" r="1.1" fill="var(--gold)"/>
        </svg>
        58 Harlow st Greenfield Ashby 4172
      </li>
    </ul>

    <div class="social">
      <span class="social-handle">TAZALUMO27</span>
      <div class="social-marks" aria-label="Social media links">
        <span class="social-mark photo"></span>
        <span class="social-mark network"></span>
      </div>
    </div>
  </section>

  <section class="card card-logo" aria-label="Business card, logo side">
    <div class="brand">
      <span class="brand-ring"></span>
      <div class="brand-text">
        <span class="brand-name">LUMO</span>
        <span class="brand-slogan">Savour the moment</span>
      </div>
    </div>
  </section>

</main>
</body>
</html>
```